business card, stationary, return address labels

acupuncture practice in private setting...www.needlecalmstudio.example.Hope for improvement in card design, especially background and arrangement of logo.Thank you,Patricia Heraghty203.297.5399

Business

Please see attached business card

```html
<!DOCTYPE html>
<html lang="en">
<head>
<meta charset="utf-8">
<title>Needle Calm Studio – Business Card</title>
<link rel="stylesheet" href="https://fonts.googleapis.com/css2?family=Questrial&display=swap">
<style>
  :root {
    --teal: #3fae98;
    --teal-deep: #36a08b;
    --teal-ink: #2f9a86;
    --paper: #ffffff;
    --stage: #ecefee;
    --rule: #9a9a9a;
    --text-light: #ffffff;
  }
  * { margin: 0; padding: 0; box-sizing: border-box; }
  html, body {
    width: 929px; height: 1200px; overflow: hidden;
    background: var(--stage);
  }
  .canvas {
    position: relative; width: 929px; height: 1200px;
    font-family: "Questrial", "Century Gothic", sans-serif;
  }
  .card-spread {
    position: absolute; left: 0; top: 0;
    width: 929px; height: 580px;
    display: flex;
    border: 1px solid var(--rule);
  }
  .card-front {
    width: 464px; height: 100%;
    background: var(--paper);
    display: flex; align-items: center; justify-content: center;
  }
  .brand-name {
    color: var(--teal-ink);
    font-size: 50px; line-height: 1.05;
    text-align: center; letter-spacing: 0.5px;
  }
  .card-back {
    position: relative;
    width: 465px; height: 100%;
    background: var(--teal);
    color: var(--text-light);
    text-align: center;
    overflow: hidden;
  }
  .calligraphy-field {
    position: absolute; inset: 0;
    width: 100%; height: 100%;
  }
  .back-content { position: relative; padding-top: 152px; }
  .holder-name { font-size: 33px; line-height: 1.1; }
  .credentials { font-size: 24px; margin-top: 6px; }
  .contact { margin-top: 60px; font-size: 22px; line-height: 1.42; }
</style>
</head>
<body>
<main class="canvas">
  <section class="card-spread">
    <div class="card-front">
      <p class="brand-name">Needle Calm<br>Studio</p>
    </div>
    <div class="card-back">
      <svg class="calligraphy-field" viewBox="0 0 465 580" role="img" aria-label="Faint Chinese calligraphy pattern across the teal background">
        <defs>
          <linearGradient id="tealWash" x1="0" y1="0" x2="0" y2="1">
            <stop offset="0" stop-color="#42b29c"/>
            <stop offset="1" stop-color="#3aa893"/>
          </linearGradient>
        </defs>
        <rect width="465" height="580" fill="url(#tealWash)"/>
      </svg>
      <div class="back-content">
        <p class="holder-name">Lorraine Vasquell</p>
        <p class="credentials">LAc,Dipi.Ac.,O.T</p>
        <p class="contact">
          48B Harlow Road, Millbrook, CT<br>
          415 682.7013<br>
          www.needlecalmstudio.example<br>
          hello@needlecalmstudio.example
        </p>
      </div>
    </div>
  </section>
</main>
</body>
</html>
```